Business card design for Brivo Engineering Tandem

We need a new business card design along with all the necessary to place an order. The company is Brivo Engineering Tandem and we recently updated our logo.

```html
<!DOCTYPE html>
<html lang="en">
<head>
<meta charset="utf-8">
<title>Brivo Engineering Tandem – Business Card</title>
<link href="https://fonts.googleapis.com/css2?family=Roboto:wght@400;500;700&display=swap" rel="stylesheet">
<style>
  :root {
    --backdrop: #3a3a3a;
    --card: #121212;
    --card-pattern-a: #1c1c1c;
    --card-pattern-b: #0c0c0c;
    --silver: #b8b8b8;
    --soft-grey: #9a9a9a;
    --accent: #e2bf2b;
  }
  * { box-sizing: border-box; margin: 0; padding: 0; }
  html, body {
    width: 1200px; height: 694px; overflow: hidden;
    background: var(--backdrop);
    font-family: "Roboto", Arial, sans-serif;
  }
  .canvas { position: relative; width: 1200px; height: 694px; }
  .card {
    position: absolute; width: 540px; height: 320px;
    border-radius: 28px; background: var(--card); overflow: hidden;
  }
  .card--front { left: 50px; top: 70px; }
  .card--back { left: 610px; top: 300px; }

  .front-pattern {
    position: absolute; inset: 0;
    background: linear-gradient(135deg, var(--card-pattern-a), var(--card-pattern-b));
  }
  .brand {
    position: absolute; left: 0; right: 0; top: 50%;
    transform: translateY(-50%);
    display: flex; align-items: center; justify-content: center; gap: 14px;
  }
  .brand-mark { width: 26px; height: 26px; background: var(--accent); }
  .brand-name {
    color: var(--silver); font-weight: 700; font-size: 30px;
    letter-spacing: 0.5px;
  }

  .back-inner { position: absolute; inset: 0; padding: 34px 40px; }
  .holder { text-align: center; }
  .holder-name { color: var(--silver); font-weight: 700; font-size: 24px; }
  .holder-role {
    color: var(--accent); font-size: 11px; letter-spacing: 4px;
    margin-top: 4px; font-weight: 500;
  }
  .contacts {
    display: flex; margin-top: 26px; align-items: stretch;
  }
  .contact { flex: 1; padding: 0 14px; }
  .contact + .contact { border-left: 1px solid var(--accent); }
  .contact-label {
    display: flex; align-items: center; gap: 7px;
    color: var(--accent); font-size: 11px; letter-spacing: 3px; font-weight: 500;
  }
  .contact-label svg { width: 15px; height: 15px; }
  .contact-value { color: var(--soft-grey); font-size: 14px; margin-top: 5px; }
  .rule { height: 1px; background: var(--accent); margin: 22px 0 14px; }
  .rule--bottom { margin: 12px 0 0; }
  .phone-label { padding-left: 14px; }
  .phone-number {
    color: var(--silver); font-weight: 700; font-size: 58px;
    padding-left: 12px; line-height: 1.05; letter-spacing: 1px;
  }
</style>
</head>
<body>
<main class="canvas">

  <section class="card card--front" aria-label="Card front">
    <div class="front-pattern" role="img" aria-label="Subtle embossed repeat of the company name across the card"></div>
    <div class="brand">
      <span class="brand-mark"></span>
      <span class="brand-name">Brivo Engineering Tandem</span>
    </div>
  </section>

  <section class="card card--back" aria-label="Card back">
    <div class="back-inner">
      <div class="holder">
        <p class="holder-name">Helen Marsh</p>
        <p class="holder-role">DIRECTOR</p>
      </div>

      <div class="contacts">
        <div class="contact">
          <p class="contact-label">
            <svg viewBox="0 0 16 16" aria-hidden="true">
              <rect x="1" y="3" width="14" height="10" fill="var(--accent)"/>
              <path d="M1 3 L8 9 L15 3" fill="none" stroke="var(--card)" stroke-width="1.4"/>
            </svg>
            E-MAIL
          </p>
          <p class="contact-value">sales@brivoengineering.co.uk</p>
        </div>
        <div class="contact">
          <p class="contact-label">
            <svg viewBox="0 0 16 16" aria-hidden="true">
              <circle cx="8" cy="8" r="7" fill="var(--accent)"/>
              <ellipse cx="8" cy="8" rx="3" ry="7" fill="none" stroke="var(--card)" stroke-width="1"/>
              <line x1="1" y1="8" x2="15" y2="8" stroke="var(--card)" stroke-width="1"/>
            </svg>
            WEB
          </p>
          <p class="contact-value">www.brivoengineering.co.uk</p>
        </div>
      </div>

      <div class="rule"></div>

      <p class="contact-label phone-label">
        <svg viewBox="0 0 16 16" aria-hidden="true">
          <path d="M2 5 Q8 1 14 5 L12.5 7 L10.5 6 L10.5 5 Q8 4 5.5 5 L5.5 6 L3.5 7 Z" fill="var(--accent)"/>
          <rect x="4" y="8" width="8" height="6" rx="1" fill="var(--accent)"/>
        </svg>
        PHONE
      </p>
      <p class="phone-number">01632 960418</p>

      <div class="rule rule--bottom"></div>
    </div>
  </section>

</main>
</body>
</html>
```